BOLD & MINIMALIST DESIGN NEEDED

We want a very bold but minimalistic business card design that is impactful and utilizes both sides of the business card. Our current logo is included for your use.

We want bold fonts and good use of negative space. We don't want the logo to overpower the design.

Target Market(s)

Professionals who are building new commercial buildings.

Industry/Entity Type

Construction

Contact Information for Business Card

Name, Title, email, office phone, cell phone, website

Font styles to use
Serif
Sans Serif

Requirements
Must have
• Bold design!

```html
<!DOCTYPE html>
<html lang="en">
<head>
<meta charset="utf-8">
<title>Veranthos Business Card</title>
<link rel="stylesheet" href="https://fonts.googleapis.com/css2?family=Noto+Serif:wght@400;700&family=Source+Sans+3:wght@400;700&display=swap">
<style>
  :root {
    --backdrop: #d3d3d3;
    --card: #ffffff;
    --card-edge: #4a4a4a;
    --ink: #111111;
    --green: #7fff12;
    --green-light: #9bff4c;
    --band-start: #1e2223;
    --band-end: #050505;
    --on-band: #ffffff;
  }
  html, body {
    margin: 0;
    padding: 0;
    width: 1200px;
    height: 1200px;
    overflow: hidden;
    background: var(--backdrop);
  }
  .sheet {
    position: relative;
    width: 1200px;
    height: 1200px;
  }
  .card {
    position: absolute;
    width: 630px;
    height: 360px;
    background: var(--card);
    outline: 1px solid var(--card-edge);
    overflow: hidden;
    font-family: "Source Sans 3", sans-serif;
    color: var(--ink);
  }
  .card--front { left: 271px; top: 160px; }
  .card--back  { left: 278px; top: 670px; }
  .card__shapes {
    position: absolute;
    inset: 0;
  }
  .shape-green { fill: var(--green); }
  .shape-green-light { fill: var(--green-light); }

  .brand {
    position: absolute;
    display: flex;
    align-items: center;
    font-family: "Source Sans 3", sans-serif;
    font-weight: 700;
    color: var(--ink);
    letter-spacing: 0.02em;
    white-space: nowrap;
  }
  .brand__mark {
    display: block;
    flex: none;
    background: var(--green);
  }
  .card--front .brand {
    left: 0; right: 0;
    top: 122px;
    justify-content: center;
    gap: 14px;
    font-size: 56px;
    line-height: 1;
  }
  .card--front .brand__mark { width: 34px; height: 34px; }
  .card--back .brand {
    left: 400px; width: 240px;
    top: 70px;
    justify-content: center;
    gap: 9px;
    font-size: 30px;
    line-height: 1;
  }
  .card--back .brand__mark { width: 20px; height: 20px; }

  .web {
    position: absolute;
    display: flex;
    align-items: center;
    color: var(--on-band);
    font-size: 23px;
    white-space: nowrap;
  }
  .card--front .web { left: 180px; top: 296px; gap: 18px; }
  .card--back .web  { left: 21px;  top: 227px; gap: 10px; }
  .web__icon { width: 25px; height: 25px; flex: none; }
  .card--front .web__icon { stroke: var(--green); }
  .card--back .web__icon  { stroke: var(--on-band); }

  .person {
    position: absolute;
    left: 22px;
    top: 46px;
    font-family: "Noto Serif", serif;
    color: var(--ink);
  }
  .person__name {
    margin: 0;
    font-size: 30px;
    font-weight: 700;
    line-height: 1;
    letter-spacing: 0.01em;
  }
  .person__post {
    margin: 9px 0 0 12px;
    font-size: 18px;
    font-weight: 400;
    line-height: 1;
  }
  .contacts {
    position: absolute;
    left: 21px;
    top: 134px;
    margin: 0;
    padding: 0;
    list-style: none;
    font-size: 23px;
    line-height: 28.5px;
  }
  .contacts__item {
    display: flex;
    align-items: center;
    gap: 9px;
    white-space: nowrap;
  }
  .contacts__icon { width: 24px; height: 24px; flex: none; }
</style>
</head>
<body>
<main class="sheet">

  <section class="card card--front" aria-label="Card front">
    <svg class="card__shapes" width="630" height="360" viewBox="0 0 630 360" aria-hidden="true">
      <defs>
        <linearGradient id="bandFront" x1="0" x2="1" y1="0" y2="0">
          <stop offset="0" stop-color="var(--band-start)"/>
          <stop offset="1" stop-color="var(--band-end)"/>
        </linearGradient>
      </defs>
      <polygon class="shape-green" points="0,196 163,360 0,360"/>
      <polygon class="shape-green-light" points="139,335 188,335 163,360"/>
      <polygon class="shape-green" points="630,196 630,360 467,360"/>
      <polygon class="shape-green-light" points="440,335 492,335 467,360"/>
      <polygon fill="url(#bandFront)" points="95,291 534,291 492,335 137,335"/>
    </svg>

    <div class="brand">
      <span class="brand__mark"></span>
      <span class="brand__name">VERANTHOS</span>
    </div>

    <div class="web">
      <svg class="web__icon" viewBox="0 0 24 24" fill="none" stroke-width="1.6" aria-hidden="true">
        <circle cx="12" cy="12" r="10.5"/>
        <ellipse cx="12" cy="12" rx="4.5" ry="10.5"/>
        <line x1="1.5" y1="12" x2="22.5" y2="12"/>
      </svg>
      <span>Your Website Address</span>
    </div>
  </section>

  <section class="card card--back" aria-label="Card back">
    <svg class="card__shapes" width="630" height="360" viewBox="0 0 630 360" aria-hidden="true">
      <defs>
        <linearGradient id="bandBack" x1="0" x2="1" y1="0" y2="0">
          <stop offset="0" stop-color="var(--band-start)"/>
          <stop offset="1" stop-color="var(--band-end)"/>
        </linearGradient>
      </defs>
      <polygon class="shape-green" points="458,165 630,165 630,291 332,291"/>
      <polygon class="shape-green-light" points="307,265 357,265 332,291"/>
      <polygon fill="url(#bandBack)" points="0,224 397,224 357,265 0,265"/>
    </svg>

    <div class="brand">
      <span class="brand__mark"></span>
      <span class="brand__name">VERANTHOS</span>
    </div>

    <div class="person">
      <h1 class="person__name">YOUR NAME</h1>
      <p class="person__post">YOUR POST</p>
    </div>

    <ul class="contacts">
      <li class="contacts__item">
        <svg class="contacts__icon" viewBox="0 0 24 24" aria-hidden="true">
          <circle cx="12" cy="12" r="12" fill="var(--ink)"/>
          <path d="M6 10.5c0-1.6 2.7-2.5 6-2.5s6 .9 6 2.5v1h-3v-1.3h-6v1.3H6z" fill="#fff"/>
          <rect x="8" y="12" width="8" height="4" rx="1" fill="#fff"/>
        </svg>
        <span>Offic Phone</span>
      </li>
      <li class="contacts__item">
        <svg class="contacts__icon" viewBox="0 0 24 24" aria-hidden="true">
          <circle cx="12" cy="12" r="12" fill="var(--ink)"/>
          <path d="M8.2 5.5l2.2 2.6-1.3 1.6c.9 1.9 2.3 3.4 4.2 4.3l1.6-1.3 2.6 2.2-1.4 2.3c-4.8-.6-8.4-4.2-9.1-9.1z" fill="#fff"/>
        </svg>
        <span>Cell Phone</span>
      </li>
      <li class="contacts__item">
        <svg class="contacts__icon" viewBox="0 0 24 24" aria-hidden="true">
          <rect x="0" y="4" width="24" height="17" rx="2" fill="var(--ink)"/>
          <path d="M3 8l9 5 9-5" fill="none" stroke="#fff" stroke-width="1.4"/>
        </svg>
        <span>Your Email Address</span>
      </li>
    </ul>

    <div class="web">
      <svg class="web__icon" viewBox="0 0 24 24" fill="none" stroke-width="1.6" aria-hidden="true">
        <circle cx="12" cy="12" r="10.5"/>
        <ellipse cx="12" cy="12" rx="4.5" ry="10.5"/>
        <line x1="1.5" y1="12" x2="22.5" y2="12"/>
      </svg>
      <span>Your Website Address</span>
    </div>
  </section>

</main>
</body>
</html>
```